The design should look similar to the uploaded example to accommodate the information needed for a business card template. I would like to see the colors orange and charcoal grey incorporated along with the logo.The following should be on the back of the card SPECIALIZING IN NEW AND USED TIRES & WHEELS FOR:- Loaders- Skid Steers- Telehandlers- Boom Lifts- Forklifs and moreELIMINATING DOWNTIMEWheel Exchange Program for New & Used Foam Filled and Solid Rubber TiresSPECIALTY SERVICES- Foam Filling Tires- Largest Tire Press in SE- ONSITE Forklift Tire Press- Boom Truck Services - Rubber Tracks

Target Market(s)

New and Existing Customers

Industry/Entity Type

Business

Contact Information for Business Card

NAMEHEAVY DUTY TIRE, LLC8470 Belvedere RoadWest Palm Beach, FL 33411P: 844-HD-TIRESF: 561-431-6469C:E: W: WWW.GRANITERIMSUPPLY-EXAMPLE.COM

Font styles to use
Sans Serif

Colors
f37122
333333

Requirements
Must have
• The logo and the information indicated for the backside of the card
Nice to have
• Keep the orange and charcoal grey colors

```html
<!DOCTYPE html>
<html lang="en">
<head>
<meta charset="utf-8">
<title>Granite Rim Supply — Business Card</title>
<link href="https://fonts.googleapis.com/css2?family=Arvo:wght@700&family=Open+Sans:wght@400;600;700&display=swap" rel="stylesheet">
<style>
  :root {
    --orange: #f37122;
    --orange-light: #f7944f;
    --charcoal: #333333;
    --slate: #3f4b58;
    --white: #ffffff;
    --stage: #d9d5cf;
  }
  * { box-sizing: border-box; margin: 0; padding: 0; }
  html, body { width: 1200px; height: 950px; overflow: hidden; }
  body {
    background: var(--stage);
    font-family: "Open Sans", Arial, sans-serif;
    position: relative;
  }
  .card {
    position: absolute;
    left: 210px;
    width: 780px;
    height: 446px;
    border-radius: 4px;
    overflow: hidden;
    box-shadow: 0 6px 18px rgba(0,0,0,.18);
  }
  /* Back side */
  .card-back {
    top: 20px;
    background: linear-gradient(100deg, var(--orange) 0%, var(--orange) 45%, var(--orange-light) 100%);
    color: var(--white);
    text-align: center;
  }
  .brand-mark {
    display: inline-flex;
    align-items: center;
    gap: 12px;
    margin-top: 38px;
  }
  .brand-dot {
    width: 44px; height: 44px; border-radius: 50%;
    background: var(--charcoal);
    flex: none;
  }
  .brand-name {
    font-family: "Arvo", Georgia, serif;
    font-weight: 700;
    font-size: 30px;
    color: var(--charcoal);
    letter-spacing: 1px;
  }
  .services { margin-top: 34px; }
  .services h2 {
    font-size: 19px;
    font-weight: 700;
    color: var(--charcoal);
    letter-spacing: .5px;
    margin-top: 18px;
  }
  .services h2:first-child { margin-top: 0; }
  .services p {
    font-size: 16.5px;
    margin-top: 6px;
    line-height: 1.35;
  }
  .services .sep { color: var(--charcoal); margin: 0 6px; }

  /* Front side */
  .card-front { top: 486px; background: var(--white); }
  .card-front .wave { position: absolute; inset: 0; width: 100%; height: 100%; }
  .front-brand {
    position: absolute; left: 44px; top: 50px;
    display: flex; align-items: center; gap: 16px;
  }
  .front-brand .brand-dot { width: 64px; height: 64px; }
  .front-brand .brand-name { font-size: 31px; line-height: 1.1; }
  .contact {
    position: absolute; right: 34px; top: 226px;
    text-align: right; color: var(--white);
  }
  .contact-name {
    font-size: 22px; font-weight: 600; color: var(--orange);
    letter-spacing: 1px; line-height: 1.3;
  }
  .contact-title { font-size: 16px; letter-spacing: 1px; margin-bottom: 8px; }
  .contact-line {
    display: flex; justify-content: flex-end; align-items: center;
    gap: 12px; font-size: 16px; line-height: 1.5;
  }
  .contact-line svg { width: 16px; height: 16px; flex: none; }
  .address {
    position: absolute; left: 40px; bottom: 26px;
    color: var(--white); font-size: 16px;
  }
</style>
</head>
<body>

<section class="card card-back" aria-label="Card back">
  <div class="brand-mark">
    <span class="brand-dot"></span>
    <span class="brand-name">GRANITE RIM</span>
  </div>
  <div class="services">
    <h2>SPECIALIZING IN NEW AND USED TIRES &amp; WHEELS FOR</h2>
    <p>Loaders<span class="sep">•</span>Skid Steers<span class="sep">•</span>Telehandlers<span class="sep">•</span>Boom Lifts<span class="sep">•</span>Forklifs and more</p>
    <h2>ELIMINATING DOWNTIME</h2>
    <p>Wheel Exchange Program for New &amp; Used Foam Filled and Solid Rubber Tires</p>
    <h2>SPECIALTY SERVICES</h2>
    <p>Foam Filling Tires<span class="sep">•</span>Largest Tire Press in SE<span class="sep">•</span>ONSITE Forklift Tire Press</p>
    <p>Boom Truck Services<span class="sep">•</span>Rubber Tracks</p>
  </div>
</section>

<section class="card card-front" aria-label="Card front">
  <svg class="wave" viewBox="0 0 780 446" preserveAspectRatio="none" aria-hidden="true">
    <path d="M0,168 C140,196 220,290 330,290 C460,290 540,148 780,106 L780,446 L0,446 Z" fill="var(--orange)"/>
    <path d="M0,178 C140,208 220,304 330,304 C460,304 540,160 780,118 L780,446 L0,446 Z" fill="var(--white)"/>
    <path d="M0,184 C140,216 220,312 330,312 C460,312 540,168 780,126 L780,446 L0,446 Z" fill="var(--slate)"/>
  </svg>

  <div class="front-brand">
    <span class="brand-dot"></span>
    <span class="brand-name">GRANITE RIM<br>SUPPLY LLC</span>
  </div>

  <div class="contact">
    <div class="contact-name">MARLA QUINN</div>
    <div class="contact-title">PRESIDENT</div>
    <div class="contact-line">844-GR-WHEEL
      <svg viewBox="0 0 16 16"><path d="M3 2h3l1 3-2 1a8 8 0 0 0 5 5l1-2 3 1v3c0 1-1 1-1 1C7 14 2 9 2 3c0 0 0-1 1-1z" fill="var(--orange)"/></svg></div>
    <div class="contact-line">836 510 4472
      <svg viewBox="0 0 16 16"><rect x="4" y="1" width="8" height="14" rx="1.5" fill="var(--orange)"/><rect x="5.5" y="3" width="5" height="8" fill="var(--slate)"/></svg></div>
    <div class="contact-line">561-278-9053
      <svg viewBox="0 0 16 16"><rect x="4" y="1" width="8" height="5" fill="var(--orange)"/><rect x="1" y="6" width="14" height="8" rx="1" fill="var(--orange)"/><rect x="4" y="9" width="8" height="2" fill="var(--slate)"/></svg></div>
    <div class="contact-line">info@graniterimsupply-example.com
      <svg viewBox="0 0 16 16"><rect x="1" y="3" width="14" height="10" rx="1" fill="var(--orange)"/><path d="M1.5 4 8 9l6.5-5" stroke="var(--slate)" stroke-width="1.3" fill="none"/></svg></div>
    <div class="contact-line">www.graniterimsupply-example.com
      <svg viewBox="0 0 16 16"><circle cx="8" cy="8" r="7" fill="var(--orange)"/><path d="M1 8h14M8 1c-3 4-3 10 0 14M8 1c3 4 3 10 0 14" stroke="var(--slate)" stroke-width="1.1" fill="none"/></svg></div>
  </div>

  <div class="address">5126 Marston Lane, Lake Harbor, FL 33412</div>
</section>

</body>
</html>
```